Create a proposal + product powerpoint

Please see the powerpoint for the slides. There are about 20 slides to be created. Rest of them are for reference and show the design that I like.

I would like to move fast on this, since I need to present it next week (in the week of April 21st).

Please download the current content from here:
https://www.parcelbrook.net/fetch/qRtVmXzLwPkNbYcD

Please make at least 4 slides with the specific content so I can assess your design style.

Target Market(s)

Business Audience and very senior technical audience
Decision Makers

Industry/Entity Type

Product

Colors
e34297
a64599

Requirements
Must have
• Should be very clean, crisp.

I like to use Icons as shown in the powerpoint.... Please see the appendix of the slide deck that shows the various icons. Most of them just have plain text, and I would like to organize so that it does not look like some is just reading text.

I would like to focus on the design aspects so that the audience is clear on how the solution works.

Every page should some graphic element based on the slides shown in the appendix.

```html
<!DOCTYPE html>
<html lang="en">
<head>
<meta charset="UTF-8">
<title>Lifecycle Management Solution</title>
<link rel="stylesheet" href="https://fonts.googleapis.com/css2?family=Exo+2:wght@400;600&family=Didact+Gothic&display=swap">
<style>
  :root {
    --pink: #e34297;
    --purple: #a64599;
    --tile-blue: #049cdc;
    --text-dark: #333333;
    --white: #ffffff;
    --wave-light: #f6e6f3;
  }
  * { margin: 0; padding: 0; box-sizing: border-box; }
  html, body { width: 1200px; height: 900px; overflow: hidden; background: var(--white); }
  .slide {
    position: relative;
    width: 1200px;
    height: 900px;
    overflow: hidden;
    background: var(--white);
    font-family: "Didact Gothic", Arial, sans-serif;
  }
  .wave-backdrop {
    position: absolute;
    left: 0; top: 330px;
    width: 1200px; height: 495px;
    background:
      radial-gradient(ellipse 70% 55% at 35% 85%, rgba(166,69,153,0.16), rgba(166,69,153,0) 70%),
      radial-gradient(ellipse 60% 45% at 85% 70%, rgba(227,66,151,0.12), rgba(227,66,151,0) 70%),
      linear-gradient(180deg, rgba(246,230,243,0) 0%, var(--wave-light) 100%);
  }
  .title-accent {
    position: absolute;
    left: 0; top: 27px;
    width: 15px; height: 69px;
    background: var(--purple);
  }
  .slide-title {
    position: absolute;
    left: 30px; top: 30px;
    font-family: "Exo 2", Arial, sans-serif;
    font-weight: 400;
    font-size: 50px;
    line-height: 60px;
    color: var(--pink);
  }
  .logo-placeholder {
    position: absolute;
    right: 44px; top: 52px;
    font-family: "Exo 2", Arial, sans-serif;
    font-weight: 600;
    font-size: 37px;
    line-height: 46px;
    color: var(--purple);
  }
  .sub-title {
    position: absolute;
    left: 32px; top: 202px;
    font-family: "Exo 2", Arial, sans-serif;
    font-weight: 600;
    font-size: 37px;
    line-height: 46px;
    color: var(--purple);
  }
  .feature-list {
    position: absolute;
    left: 33px; top: 290px;
    list-style: none;
  }
  .feature-item {
    display: flex;
    align-items: center;
    height: 46px;
    margin-bottom: 33.5px;
    font-size: 34px;
    color: var(--text-dark);
    letter-spacing: 0.5px;
  }
  .bullet-mark { width: 37px; height: 37px; margin-right: 25px; flex: none; }
  .icon-grid {
    position: absolute;
    left: 680px; top: 256px;
    display: grid;
    grid-template-columns: 234px 234px;
    grid-template-rows: 234px 234px;
    gap: 14px;
  }
  .icon-tile {
    background: var(--tile-blue);
    display: flex;
    align-items: center;
    justify-content: center;
  }
  .icon-tile svg { width: 140px; height: 140px; }
  .footer-line {
    position: absolute;
    left: 0; top: 822px;
    width: 1200px; height: 6px;
    background: var(--purple);
  }
  .footer-band {
    position: absolute;
    left: 0; top: 828px;
    width: 1200px; height: 72px;
    background: var(--pink);
  }
  .copyright {
    position: absolute;
    right: 18px; top: 850px;
    font-family: "Exo 2", Arial, sans-serif;
    font-size: 21px;
    line-height: 26px;
    color: var(--white);
  }
</style>
</head>
<body>
<main class="slide">
  <div class="wave-backdrop" role="img" aria-label="Soft pink and purple flowing line waves decorating the lower background"></div>

  <div class="title-accent"></div>
  <h1 class="slide-title">Lifecycle Management Solution</h1>
  <div class="logo-placeholder">LOGO HERE</div>

  <h2 class="sub-title">SUB Text title here</h2>

  <ul class="feature-list">
    <li class="feature-item">
      <svg class="bullet-mark" viewBox="0 0 36 36" aria-hidden="true"><circle cx="18" cy="18" r="18" fill="var(--purple)"/><path d="M14 10 L23 18 L14 26" fill="none" stroke="#fff" stroke-width="5" stroke-linecap="round" stroke-linejoin="round"/></svg>
      Code promotion
    </li>
    <li class="feature-item">
      <svg class="bullet-mark" viewBox="0 0 36 36" aria-hidden="true"><circle cx="18" cy="18" r="18" fill="var(--purple)"/><path d="M14 10 L23 18 L14 26" fill="none" stroke="#fff" stroke-width="5" stroke-linecap="round" stroke-linejoin="round"/></svg>
      Change Management
    </li>
    <li class="feature-item">
      <svg class="bullet-mark" viewBox="0 0 36 36" aria-hidden="true"><circle cx="18" cy="18" r="18" fill="var(--purple)"/><path d="M14 10 L23 18 L14 26" fill="none" stroke="#fff" stroke-width="5" stroke-linecap="round" stroke-linejoin="round"/></svg>
      Troubleshooting
    </li>
    <li class="feature-item">
      <svg class="bullet-mark" viewBox="0 0 36 36" aria-hidden="true"><circle cx="18" cy="18" r="18" fill="var(--purple)"/><path d="M14 10 L23 18 L14 26" fill="none" stroke="#fff" stroke-width="5" stroke-linecap="round" stroke-linejoin="round"/></svg>
      Build and test automation
    </li>
    <li class="feature-item">
      <svg class="bullet-mark" viewBox="0 0 36 36" aria-hidden="true"><circle cx="18" cy="18" r="18" fill="var(--purple)"/><path d="M14 10 L23 18 L14 26" fill="none" stroke="#fff" stroke-width="5" stroke-linecap="round" stroke-linejoin="round"/></svg>
      Audit Analysis
    </li>
  </ul>

  <div class="icon-grid">
    <div class="icon-tile">
      <svg viewBox="0 0 100 100" aria-label="Presentation board icon" role="img">
        <rect x="6" y="12" width="88" height="7" rx="2" fill="#fff"/>
        <rect x="46" y="6" width="8" height="8" fill="#fff"/>
        <path fill="#fff" fill-rule="evenodd" d="M12 19 H88 V70 H12 Z M20 26 V63 H80 V26 Z"/>
        <rect x="46" y="70" width="8" height="22" fill="#fff"/>
        <path d="M36 74 L24 90" stroke="#fff" stroke-width="7" stroke-linecap="round"/>
        <path d="M64 74 L76 90" stroke="#fff" stroke-width="7" stroke-linecap="round"/>
      </svg>
    </div>
    <div class="icon-tile">
      <svg viewBox="0 0 100 100" aria-label="Set square icon" role="img">
        <path fill="#fff" fill-rule="evenodd" d="M95 4 V95 H4 Z M82 38 V82 H38 Z"/>
        <g stroke="var(--tile-blue)" stroke-width="2.5">
          <path d="M95 20 H88 M95 32 H90 M95 44 H88 M95 56 H90 M95 68 H88"/>
          <path d="M20 95 V88 M32 95 V90 M44 95 V88 M56 95 V90 M68 95 V88"/>
        </g>
      </svg>
    </div>
    <div class="icon-tile">
      <svg viewBox="0 0 100 100" aria-label="Puzzle piece icon" role="img">
        <path fill="#fff" d="M30 8 C30 0 48 0 46 10 C45 16 40 18 40 22 H64 V46 C68 46 70 40 76 40 C88 40 88 58 76 58 C70 58 68 52 64 52 V80 H42 C42 76 48 74 48 68 C48 56 30 56 30 68 C30 74 36 76 36 80 H14 V52 C10 52 8 58 2 58 C-4 58 -4 40 2 40 C8 40 10 46 14 46 V22 H36 C36 18 30 16 30 8 Z" transform="translate(10 8)"/>
      </svg>
    </div>
    <div class="icon-tile">
      <svg viewBox="0 0 100 100" aria-label="Compass icon" role="img">
        <circle cx="50" cy="50" r="42" fill="none" stroke="#fff" stroke-width="9"/>
        <path d="M50 14 V24 M50 76 V86 M14 50 H24 M76 50 H86" stroke="#fff" stroke-width="4"/>
        <path d="M70 28 L54 54 L46 46 Z" fill="#fff"/>
        <path d="M30 72 L46 46 L54 54 Z" fill="#fff"/>
        <circle cx="50" cy="50" r="3" fill="var(--tile-blue)"/>
      </svg>
    </div>
  </div>

  <div class="footer-line"></div>
  <footer class="footer-band"></footer>
  <div class="copyright">Copyright text here</div>
</main>
</body>
</html>
```